My business is Property developing Stationary

I want business card and stationery. Please have the formate so I can edit details on card and stationary.

Please see my logo and on the back of the card I want it same red as my logo and I will provide copy that I want on the back of the card.

Also need an email signature

On the business card and email signature add below copy:
Project Management- Acquisitions- Syndicates- Joint Ventures

Target Market(s)

Property investors

Industry/Entity Type

Business

Requirements
Must have
• Reflect my Logo

```html
<!DOCTYPE html>
<html lang="en">
<head>
<meta charset="utf-8">
<title>Varelo Business Card</title>
<link rel="stylesheet" href="https://fonts.googleapis.com/css2?family=Mulish:wght@400;700&display=swap">
<style>
  :root {
    --brand-red: #d93a2b;
    --ink: #2b2b2b;
    --paper: #f7f7f7;
    --backdrop: #2c2c2c;
    --stripe-black: #1c1c1c;
    --stripe-grey: #e6e6e6;
    --stripe-grey-soft: #eeeeee;
    --white: #ffffff;
  }
  * { box-sizing: border-box; margin: 0; padding: 0; }
  html, body { width: 1200px; height: 1001px; overflow: hidden; }
  body {
    background: var(--backdrop);
    font-family: "Mulish", sans-serif;
    position: relative;
  }
  .card {
    position: absolute;
    width: 580px;
    height: 325px;
    overflow: hidden;
  }
  .card-decor {
    position: absolute;
    inset: 0;
    width: 100%;
    height: 100%;
  }
  /* front */
  .card-front { left: 201px; top: 148px; background: var(--paper); }
  .holder-name {
    position: absolute; left: 28px; top: 58px;
    color: var(--brand-red); font-weight: 700; font-size: 19px; letter-spacing: 0.5px;
  }
  .holder-role {
    position: absolute; left: 28px; top: 82px;
    color: var(--ink); font-size: 15px;
  }
  .contact-list {
    position: absolute; left: 28px; top: 126px; list-style: none;
  }
  .contact-list li {
    display: flex; align-items: center; gap: 8px;
    height: 18px; font-size: 14px; color: var(--ink);
  }
  .contact-icon { width: 15px; height: 15px; flex: none; }
  .address {
    position: absolute; left: 28px; top: 218px;
    font-size: 14px; line-height: 17px; color: var(--ink); font-style: normal;
  }
  .services {
    position: absolute; left: 28px; top: 276px;
    font-size: 12.5px; color: var(--ink);
  }
  .wordmark {
    position: absolute; font-weight: 700; letter-spacing: 1px; line-height: 1;
  }
  .card-front .wordmark { left: 300px; top: 48px; font-size: 50px; color: var(--brand-red); }
  /* back */
  .card-back { left: 419px; top: 549px; background: var(--brand-red); }
  .card-back .wordmark { left: 272px; top: 70px; font-size: 50px; color: var(--white); }
  .back-web {
    position: absolute; right: 54px; bottom: 40px;
    font-size: 15px; color: var(--white);
  }
</style>
</head>
<body>

<section class="card card-front" aria-label="Business card front">
  <svg class="card-decor" viewBox="0 0 638 357" preserveAspectRatio="none" aria-hidden="true">
    <polygon points="410,357 638,129 638,175 456,357" fill="var(--stripe-grey-soft)"/>
    <polygon points="456,357 638,175 638,215 496,357" fill="var(--stripe-grey)"/>
    <rect x="0" y="338" width="496" height="19" fill="var(--brand-red)"/>
    <polygon points="496,357 638,215 638,248 529,357" fill="var(--white)"/>
    <polygon points="508,357 638,247 638,283 545,357" fill="var(--stripe-black)"/>
    <polygon points="545,357 638,283 638,308 577,357" fill="var(--white)"/>
    <polygon points="566,357 638,307 638,357" fill="var(--brand-red)"/>
  </svg>

  <div class="wordmark">VARELO</div>

  <h1 class="holder-name">DANIEL VARELO</h1>
  <p class="holder-role">Managing Director</p>

  <ul class="contact-list">
    <li>
      <svg class="contact-icon" viewBox="0 0 16 16" aria-hidden="true"><rect width="16" height="16" rx="3" fill="var(--brand-red)"/><rect x="5" y="3" width="6" height="10" rx="1" fill="none" stroke="#fff" stroke-width="1.3"/></svg>
      +61 (0) 400 218 530
    </li>
    <li>
      <svg class="contact-icon" viewBox="0 0 16 16" aria-hidden="true"><rect width="16" height="16" rx="3" fill="var(--brand-red)"/><path d="M5 3.5l2 2-1 1.3c.7 1.4 1.8 2.5 3.2 3.2l1.3-1 2 2-1.3 1.5C7.8 12.3 3.7 8.2 3.5 4.8z" fill="#fff"/></svg>
      +61 (0) 400 218 900
    </li>
    <li>
      <svg class="contact-icon" viewBox="0 0 16 16" aria-hidden="true"><rect width="16" height="16" rx="3" fill="var(--brand-red)"/><rect x="3" y="4.5" width="10" height="7" fill="none" stroke="#fff" stroke-width="1.2"/><path d="M3 4.5l5 4 5-4" fill="none" stroke="#fff" stroke-width="1.2"/></svg>
      info@varelo.com
    </li>
    <li>
      <svg class="contact-icon" viewBox="0 0 16 16" aria-hidden="true"><rect width="16" height="16" rx="3" fill="var(--brand-red)"/><circle cx="8" cy="8" r="4.8" fill="none" stroke="#fff" stroke-width="1.1"/><ellipse cx="8" cy="8" rx="2" ry="4.8" fill="none" stroke="#fff" stroke-width="1"/><path d="M3.2 8h9.6" stroke="#fff" stroke-width="1"/></svg>
      www.varelo.com
    </li>
  </ul>

  <address class="address">Level 12, Harbour House<br>18 Kent Lane, Sydney</address>

  <p class="services">Project Management Acquisitions Syndicates Joint Venture</p>
</section>

<section class="card card-back" aria-label="Business card back">
  <svg class="card-decor" viewBox="0 0 638 357" preserveAspectRatio="none" aria-hidden="true">
    <polygon points="0,52 305,357 265,357 0,92" fill="var(--white)"/>
    <polygon points="0,92 265,357 222,357 0,135" fill="var(--stripe-black)"/>
    <polygon points="0,135 222,357 182,357 0,175" fill="var(--white)"/>
  </svg>
  <div class="wordmark">VARELO</div>
  <p class="back-web">www.varelo.com</p>
</section>

</body>
</html>
```